Zielgruppe
Das Buch ist für Kinder ab 10. Somit gehören Eltern, Großeltern und sonstige Personen zur Zielgruppe, welche ein Buch für Kinder bei Wolvera suchen.
Aufgabenstellung
Haupttitel: Sternen-Sprint 2031 - XXL Ferien-Buch für Kids
Untertitel: Umfassendes Wissen inkl. Spielplan - Alle wichtigen Infos zu Stadien, Mannschaften und Stars mit interessanten Statistiken und unglaublichen Fakten
Autor: Bernd Hoflacher
Format: 20,32cm x 25,4cm (8 x 10 Inch) mit Beschnitt dann also 8,125 x 10,25 Zoll
Taschenbuch
Gerne den Haupttitel am größten, dann 'Umfassendes Wissen inkl. Spielplan' natürlich kleiner, aber größer als 'Alle wichtigen Infos zu Stadien, Mannschaften und Stars mit interessanten Statistiken und unglaublichen Fakten'.
Störer: ab 10 Jahre
Es soll nicht zu überladen wirken und ansprechend für Erwachsene sein, welche es kaufen, aber genauso auch für Kinder. Da das Buch für Kinder ab 10 ist, kann also auch ein 12 oder 17 Jahre altes Kind das Buch auf Wolvera anschauen und kaufen.
Anbei ist eine Grafik eines Fußballers in Neonfarben. Diese bitte mittig unten platzieren.
Gerne auch Vorschläge ohne die Grafik machen.
Falls du Stockfotos verwenden willst, dann bitte von Pixelhort.
Anbei sind auch zwei Screenshots von aktuellen Konkurrenzbüchern. Es werden sicherlich noch viel mehr Bücher erscheinen. Bitte achtet darauf, dass sich das Cover von der Konkurrenz abhebt. Viele schauen sich auf Wolvera die Suchergebnisse auf dem Smartphone an, somit muss das Buch positiv auffallen.
Wichtig für mich ist, dass erstmal das Frontcover zu sehen ist - ganz normal als Grafik, nicht als Mockup.
Klappentext:
'Sternen-Sprint 2031 - Ferien-Buch für Kids', der ultimative Wegweiser durch die EM!
Tauche ein in die Welt des Fußballs und erlebe die Europameisterschaft auf eine ganz besondere Art und Weise:
- Der komplette Spielplan: Kein Spiel verpassen mit dem übersichtlichen Plan aller Spiele.
- Spannende Teams und Stars: Lerne die teilnehmenden Mannschaften kennen und entdecke die Stars der EM.
- Glänzende Stadien: Erkunde ..

```html
<!DOCTYPE html>
<html lang="de">
<head>
<meta charset="utf-8">
<title>Sternen-Sprint 2031 – Ferien-Buch für Kids</title>
<link href="https://fonts.googleapis.com/css2?family=Bebas+Neue&family=Oswald:wght@500;600&family=Rubik+Dirt&display=swap" rel="stylesheet">
<style>
  :root {
    --bg: #000000;
    --teal: #36bac7;
    --yellow: #f5c316;
    --red: #c7161d;
    --ink: #0b0b0b;
    --white: #ffffff;
    --art-teal: #2fb4c8;
    --art-purple: #5a2a6e;
    --art-orange: #f07a1c;
    --art-red: #e23a1e;
    --art-yellow: #f8d81a;
  }
  html, body { margin: 0; padding: 0; overflow: hidden; background: var(--bg); }
  .cover {
    position: relative;
    width: 960px;
    height: 1200px;
    overflow: hidden;
    background: var(--bg);
  }
  .artwork {
    position: absolute;
    left: 120px;
    top: 340px;
    width: 620px;
    height: 740px;
    border-radius: 46% 46% 38% 38% / 30% 30% 22% 22%;
    background:
      radial-gradient(ellipse 26% 30% at 56% 40%, var(--art-teal) 0%, var(--art-purple) 70%, rgba(90,42,110,0) 100%),
      radial-gradient(ellipse 48% 20% at 42% 84%, var(--art-yellow) 0%, var(--art-orange) 60%, rgba(240,122,28,0) 100%),
      radial-gradient(ellipse 28% 34% at 24% 58%, var(--art-red) 0%, rgba(226,58,30,0) 100%),
      linear-gradient(180deg, rgba(47,180,200,0.55) 0%, rgba(90,42,110,0.7) 45%, rgba(240,122,28,0.8) 75%, rgba(248,216,26,0.6) 100%);
    -webkit-mask-image: radial-gradient(ellipse 50% 50% at 50% 50%, #000 70%, transparent 100%);
            mask-image: radial-gradient(ellipse 50% 50% at 50% 50%, #000 70%, transparent 100%);
  }
  .author {
    position: absolute;
    top: 36px;
    width: 100%;
    text-align: center;
    margin: 0;
    font: 400 52px/1 "Bebas Neue", sans-serif;
    letter-spacing: 1px;
    color: var(--teal);
  }
  .title {
    position: absolute;
    top: 86px;
    left: 0;
    width: 100%;
    margin: 0;
    text-align: center;
    font-family: "Rubik Dirt", sans-serif;
    font-weight: 400;
    color: var(--teal);
  }
  .title-line { display: block; line-height: 1; white-space: nowrap; transform-origin: center; }
  .title-line--one { font-size: 176px; transform: scaleX(0.76); }
  .title-line--two { font-size: 176px; margin-top: -28px; transform: scaleX(0.6); }
  .series {
    position: absolute;
    top: 380px;
    margin: 0;
    font: 400 92px/1 "Rubik Dirt", sans-serif;
    color: var(--yellow);
    white-space: nowrap;
  }
  .series--left { left: 66px; transform: scaleX(0.56); transform-origin: left; }
  .series--right { right: 44px; transform: scaleX(0.8); transform-origin: right; }
  .subtitle {
    position: absolute;
    top: 478px;
    right: 38px;
    width: 290px;
    margin: 0;
    text-align: center;
    font: 500 54px/58px "Oswald", sans-serif;
    color: var(--yellow);
    transform: scaleX(0.88);
    transform-origin: center;
  }
  .age-badge {
    position: absolute;
    left: 668px;
    top: 840px;
    width: 240px;
    height: 230px;
  }
  .age-badge svg { position: absolute; inset: 0; }
  .age-badge-text {
    position: absolute;
    inset: 0;
    display: flex;
    flex-direction: column;
    align-items: center;
    justify-content: center;
    font: 500 44px/46px "Oswald", sans-serif;
    color: var(--white);
    transform: scaleX(0.85);
  }
  .info-band {
    position: absolute;
    left: 0;
    bottom: 0;
    width: 100%;
    height: 102px;
    background: var(--teal);
    display: flex;
    align-items: center;
    justify-content: center;
  }
  .info-band p {
    margin: 0;
    text-align: center;
    font: 500 31px/36px "Oswald", sans-serif;
    color: var(--ink);
    transform: scaleX(0.82);
    white-space: nowrap;
  }
</style>
</head>
<body>
<main class="cover">
  <div class="artwork" role="img" aria-label="Neonfarbene Illustration eines Fußballspielers beim Schuss, umgeben von gelben und roten Farbspritzern"></div>

  <p class="author">BERND HOFLACHER</p>

  <h1 class="title">
    <span class="title-line title-line--one">STERNEN-</span>
    <span class="title-line title-line--two">SPRINT-2031</span>
  </h1>

  <p class="series series--left">FERIEN-BUCH</p>
  <p class="series series--right">FÜR KIDS</p>

  <h2 class="subtitle">UMFASSENDES WISSEN INKL. SPIELPLAN -</h2>

  <div class="age-badge">
    <svg viewBox="0 0 230 230" aria-hidden="true">
      <path fill="var(--red)" d="M112 28c22 4 30 -14 52 2c18 14 4 30 24 42c22 14 34 26 26 52c-6 20 -20 18 -14 40c6 22 -14 38 -36 34c-20 -4 -28 14 -50 14c-24 0 -28 -20 -50 -22c-24 -2 -40 -14 -34 -38c4 -18 -14 -26 -8 -50c6 -24 28 -22 36 -42c8 -22 30 -36 54 -32z"/>
      <circle cx="20" cy="92" r="7" fill="var(--red)"/>
      <circle cx="214" cy="150" r="8" fill="var(--red)"/>
      <circle cx="200" cy="208" r="6" fill="var(--red)"/>
      <circle cx="44" cy="200" r="5" fill="var(--red)"/>
    </svg>
    <div class="age-badge-text"><span>AB</span><span>10 JAHRE</span></div>
  </div>

  <footer class="info-band">
    <p>ALLE WICHTIGEN INFOS ZU STADIEN, MANNSCHAFTEN UND<br>STARS MIT INTERESSANTEN STATISTIKEN UND UNGLAUBLICHEN FAKTEN</p>
  </footer>
</main>
</body>
</html>
```